Hybrid Seed corn and Soybean Sales business needs a website.

We here at "KW Grain" feel that we need a website to show a very professional side to our customer base. Although no actual ordering will take place on this website, we would like to put Plot and field trail data on the website. Along with a brief page for each of our hybrids and a place for customers to sign up for a newsletter. The company we sell hybrids for is MolvanGrain.com... Im not sure how this process works as far as myself updating the information or having the data actually put on the website, but feel free to contact me if you need the information. I will attach the logo for the company, (KW Grain).

Target Market(s)

Farmers, "Producers", Corn and soybean production

Industry/Entity Type

Business

Coding

Coded - Design and coding required

Number of Pages Required

5+ page

Colors
f78f20
ffffff

Requirements
Nice to have
• Similar layout to http://www.molvangrain.com/
• And it would be nice to incorporate our story into the website
• http://www.molvangrain.com/our-story/molvan-today/

```html
<!DOCTYPE html>
<html lang="en">
<head>
<meta charset="utf-8">
<title>KW Grain — Hybrid Seeds of Corn &amp; Soybean</title>
<link href="https://fonts.googleapis.com/css2?family=Open+Sans:wght@400;600;700&family=Roboto:wght@400;500&display=swap" rel="stylesheet">
<style>
:root{
  --orange:#f78f20;
  --orange-deep:#e0741a;
  --green:#5fa62a;
  --green-light:#7cc242;
  --ink:#222;
  --text:#555;
  --muted:#888;
  --line:#d6d6d6;
  --band:#f2f2f2;
  --white:#fff;
}
*{box-sizing:border-box;margin:0;padding:0}
html,body{width:800px;height:1200px;overflow:hidden;background:var(--white)}
body{position:relative;font-family:"Open Sans",sans-serif;color:var(--text)}
.abs{position:absolute}

/* header */
.brand{left:66px;top:30px;display:flex;align-items:center;gap:8px}
.brand-dot{width:26px;height:26px;border-radius:50%;background:var(--orange)}
.brand-name{font-size:22px;font-weight:700;color:var(--orange);letter-spacing:1px}
.newsletter{left:376px;top:30px;display:flex;align-items:center;gap:6px}
.newsletter-label{font-size:9px;line-height:11px;color:#444;letter-spacing:.5px}
.newsletter-label b{display:block;color:var(--orange);font-weight:600}
.field{width:99px;height:18px;border:1px solid #ccc;font-size:7px;color:#888;padding:4px 6px;margin-left:4px}
.subscribe{width:56px;height:18px;background:var(--orange);color:#fff;font-size:7.5px;text-align:center;line-height:18px;margin-left:4px}
.nav{left:379px;top:72px;display:flex;font-size:9px;color:#333}
.nav a{color:inherit;text-decoration:none;padding:2px 12px 16px;position:relative}
.nav a.active{color:var(--orange)}
.nav a.active::after{content:"";position:absolute;left:0;right:0;bottom:0;height:3px;background:var(--orange)}

/* hero */
.hero{left:0;top:101px;width:800px;height:356px;background:linear-gradient(180deg,#6a6f5a 0%,#55523f 40%,#4a4234 100%)}
.hero-hands{left:310px;top:140px;width:210px;height:216px;border-radius:90px 90px 0 0;background:radial-gradient(circle at 50% 45%,#e7c98a 0%,#d9a577 55%,rgba(200,150,110,0) 75%)}
.hero-card{left:66px;top:151px;width:309px;height:149px;background:var(--green);padding:20px 24px}
.hero-card h1{font-family:"Roboto",sans-serif;font-weight:500;font-size:26px;line-height:30px;color:#fff}
.hero-card p{margin-top:12px;font-size:10px;line-height:15px;color:#f0f7e8}
.hero-fold{left:335px;top:151px}
.hero-arrow{top:277px}

/* about */
.about-title{left:66px;top:492px;font-size:17px;font-weight:700;color:var(--ink)}
.about-lead{left:65px;top:518px;font-size:13px;color:#333}
.about-body{left:66px;top:547px;width:344px;font-size:8.2px;line-height:12.6px;color:#666}
.btn{left:66px;top:646px;width:107px;height:22px;background:var(--orange);color:#fff;font-size:9px;font-weight:700;text-align:center;line-height:22px}
.video{left:442px;top:490px;width:293px;height:158px;background:radial-gradient(ellipse at 55% 80%,#f4b23a 0%,#b8521c 25%,#3b1d10 60%,#1c110b 100%)}
.video-play{left:568px;top:563px;width:18px;height:18px;background:var(--green);opacity:.9}
.player{left:442px;top:652px;width:293px;height:24px;display:flex;align-items:center;font-size:6.5px;color:#999}
.player-btn{width:25px;height:24px;background:var(--orange);display:flex;align-items:center;justify-content:center}
.track{width:131px;height:3px;background:#ccc;margin:0 8px;position:relative}
.track span{position:absolute;left:0;top:0;bottom:0;width:67%;background:#555}

/* partners */
.partners{left:0;top:720px;width:800px;height:158px;background:var(--band)}
.partner{top:760px;width:176px;height:76px;background:#fff;box-shadow:0 1px 3px rgba(0,0,0,.12);display:flex;align-items:center;justify-content:center;gap:6px;font-weight:700}
.partner-mark{width:14px;height:14px;border-radius:50%}

/* news */
.news-title{left:66px;top:906px;font-size:17px;font-weight:700;color:var(--ink)}
.news-nav{left:704px;top:910px;display:flex;gap:3px}
.news-item{top:946px;width:220px;display:flex;gap:8px}
.news-img{width:93px;height:70px;flex:none}
.news-item h3{font-size:10px;font-weight:400;color:#333;margin-top:-1px}
.news-date{font-size:6.5px;color:#333;margin:4px 0}
.news-item p{font-size:6.5px;line-height:9.3px;color:#666}
.news-more{font-size:6.5px;color:#777;margin-top:5px}

/* footer */
.footer{left:0;top:1077px;width:800px;height:123px;background:linear-gradient(180deg,var(--orange-deep),#e36f15)}
.footer-links{left:66px;top:1101px;display:flex;align-items:center;font-size:7.5px;color:#fff}
.footer-links .pill{border:1px solid #fff;border-radius:10px;padding:4px 8px}
.footer-links span.sep{margin:0 9px}
.footer-line{left:66px;top:1136px;width:676px;height:1px;background:rgba(255,255,255,.3)}
.social{left:667px;top:1100px;display:flex;gap:10px}
.social i{width:10px;height:10px;border-radius:50%;background:#fff;display:block}
.tip{left:672px;top:1121px;background:#3e9a36;color:#fff;font-size:6px;font-weight:700;padding:3px 6px;border-radius:8px}
.contact{top:1154px;display:flex;align-items:center;gap:6px;font-size:6.5px;line-height:9px;color:#fff}
.contact-ico{width:15px;height:15px;border-radius:50%;background:#fff;display:flex;align-items:center;justify-content:center;flex:none}
.copy{left:581px;top:1158px;font-size:7px;color:#fff}
</style>
</head>
<body>

<header>
  <div class="abs brand"><span class="brand-dot"></span><span class="brand-name">KW GRAIN</span></div>
  <div class="abs newsletter">
    <svg width="18" height="18" viewBox="0 0 18 18"><path d="M2 7l7-5 7 5v9H2z" fill="var(--green)"/><path d="M2 7l7 5 7-5" fill="none" stroke="#fff" stroke-width="1.2"/></svg>
    <div class="newsletter-label">sign up for a<b>NEWSLETTER</b></div>
    <div class="field">Name</div>
    <div class="field">Email</div>
    <div class="subscribe">SUBSRIBE</div>
  </div>
  <nav class="abs nav">
    <a class="active">Home</a><a>Our Story</a><a>Gallery</a><a>Products</a><a>Blog &amp; Events</a><a>Contact</a>
  </nav>
</header>

<section>
  <div class="abs hero" role="img" aria-label="Rows of young corn plants in a tilled field"></div>
  <div class="abs hero-hands" role="img" aria-label="Cupped hands holding soybeans"></div>
  <div class="abs hero-card">
    <h1>We sell hybrid seeds<br>of Corn &amp; Soybean.</h1>
    <p>Lorem ipsum dolor sit amet, consectetur adipiscing elit.<br>Nam vestibulum nec ex feugiat congue.</p>
  </div>
  <svg class="abs hero-fold" width="40" height="34" viewBox="0 0 40 34"><path d="M0 0h40L40 34z" fill="var(--green-light)"/></svg>
  <svg class="abs hero-arrow" style="left:16px" width="14" height="26" viewBox="0 0 14 26"><path d="M12 2L2 13l10 11" fill="none" stroke="rgba(255,255,255,.6)" stroke-width="2"/></svg>
  <svg class="abs hero-arrow" style="left:768px" width="14" height="26" viewBox="0 0 14 26"><path d="M2 2l10 11L2 24" fill="none" stroke="rgba(255,255,255,.6)" stroke-width="2"/></svg>
</section>

<section>
  <h2 class="abs about-title">About Us</h2>
  <p class="abs about-lead">Lorem ipsum dolor sit amet, consectetur adipiscing elit.</p>
  <p class="abs about-body">Lorem ipsum dolor sit amet, consectetur adipiscing elit. Nullam auctor, nisl tincidunt tristique cursus, felis lectus placerat urna, non viverra lacus dolor iaculis tellus. Aliquam tincidunt gravida tortor non dapibus. Nam imperdiet enim porta, mattis nisi a, mattis eros. Class aptent taciti sociosqu ad litora torquent per conubia nostra, per inceptos himenaeos. Vestibulum pellentesque arcu laoreet, euismod eros id, mollis libero. Nulla facilisi. Maecenas quis semper ex.</p>
  <div class="abs btn">READ MORE</div>
  <div class="abs video" role="img" aria-label="Video still of a sunset over farmland"></div>
  <div class="abs video-play"><svg width="18" height="18" viewBox="0 0 18 18"><path d="M7 5l5 4-5 4z" fill="#fff"/></svg></div>
  <div class="abs player">
    <div class="player-btn"><svg width="8" height="8" viewBox="0 0 8 8"><path d="M1 0l6 4-6 4z" fill="#fff"/></svg></div>
    <span style="margin-left:7px">00:15:35</span>
    <div class="track"><span></span></div>
    <span>2:15:35</span>
    <svg style="margin-left:5px" width="30" height="7" viewBox="0 0 30 7"><path d="M0 2h2l3-2v7L2 5H0z" fill="#888"/><g fill="#5fb0c9"><rect x="11" y="1" width="1.2" height="6"/><rect x="14" y="1" width="1.2" height="6"/><rect x="17" y="1" width="1.2" height="6"/><rect x="20" y="1" width="1.2" height="6"/></g><g fill="#ccc"><rect x="23" y="1" width="1.2" height="6"/><rect x="26" y="1" width="1.2" height="6"/></g></svg>
    <svg style="margin-left:9px" width="9" height="8" viewBox="0 0 9 8"><rect x=".5" y=".5" width="8" height="7" fill="none" stroke="#888"/><rect x="2.5" y="2.5" width="4" height="3" fill="#888"/></svg>
  </div>
</section>

<section>
  <div class="abs partners"></div>
  <div class="abs partner" style="left:109px"><span class="partner-mark" style="background:#3b9a3a"></span><span style="color:#1f6e73;font-size:17px">Verdance</span></div>
  <div class="abs partner" style="left:303px"><span class="partner-mark" style="background:#d9262c"></span><span style="color:#222;font-size:8px">Ridgefield AgroSciences</span></div>
  <div class="abs partner" style="left:498px"><span class="partner-mark" style="background:var(--orange)"></span><span style="color:#222;font-size:20px">molvan</span></div>
</section>

<section>
  <h2 class="abs news-title">Latest News</h2>
  <div class="abs news-nav">
    <svg width="14" height="14" viewBox="0 0 14 14"><circle cx="7" cy="7" r="6" fill="none" stroke="#555"/><path d="M10 7H4m2.5-2.5L4 7l2.5 2.5" fill="none" stroke="#555"/></svg>
    <svg width="14" height="14" viewBox="0 0 14 14"><circle cx="7" cy="7" r="6" fill="none" stroke="var(--orange)"/><path d="M4 7h6M7.5 4.5L10 7 7.5 9.5" fill="none" stroke="var(--orange)"/></svg>
  </div>
  <article class="abs news-item" style="left:66px">
    <div class="news-img" role="img" aria-label="Hand planting corn kernels in dark soil" style="background:linear-gradient(135deg,#2b2520,#5a4a3a)"></div>
    <div><h3>Lorem ipsum dolor sit</h3><div class="news-date">15/05/15 &nbsp;-&nbsp; Friday</div><p>Pellentesque laoreet iaculis tempor. Sed ultricies ullamcorper magna, vel tempus lacus dapibus ac.</p><div class="news-more">Read More &#9679;</div></div>
  </article>
  <article class="abs news-item" style="left:293px">
    <div class="news-img" role="img" aria-label="Hand holding grain over a wheat field under blue sky" style="background:linear-gradient(180deg,#4f8fd0,#c7a05a 60%,#a07a3c)"></div>
    <div><h3>Lorem ipsum dolor sit</h3><div class="news-date">15/05/15 &nbsp;-&nbsp; Friday</div><p>Pellentesque laoreet iaculis tempor. Sed ultricies ullamcorper magna, vel tempus lacus dapibus ac.</p><div class="news-more">Read More &#9679;</div></div>
  </article>
  <article class="abs news-item" style="left:521px">
    <div class="news-img" role="img" aria-label="Close-up of white, yellow and purple corn cobs" style="background:linear-gradient(135deg,#eee9d8,#e8c24a 55%,#6a2a4a)"></div>
    <div><h3>Lorem ipsum dolor sit</h3><div class="news-date">15/05/15 &nbsp;-&nbsp; Friday</div><p>Pellentesque laoreet iaculis tempor. Sed ultricies ullamcorper magna, vel tempus lacus dapibus ac.</p><div class="news-more">Read More &#9679;</div></div>
  </article>
</section>

<footer>
  <div class="abs footer"></div>
  <nav class="abs footer-links">
    <span class="pill">HOME</span><span style="margin-left:12px">About</span><span class="sep">|</span>Service<span class="sep">|</span>Sitemap<span class="sep">|</span>FAQS<span class="sep">|</span>Contact Us
  </nav>
  <div class="abs social"><i></i><i></i><i></i><i></i></div>
  <div class="abs tip">PINFOLIO</div>
  <div class="abs footer-line"></div>
  <div class="abs contact" style="left:66px">
    <span class="contact-ico"><svg width="8" height="9" viewBox="0 0 8 9"><path d="M4 9S0 5 0 3.2A4 3.5 0 0 1 8 3.2C8 5 4 9 4 9z" fill="var(--orange)"/><circle cx="4" cy="3.3" r="1.2" fill="#fff"/></svg></span>
    <span>14 Harrow Lane, Millbrook, Prairie County<br>5203, United States</span>
  </div>
  <div class="abs contact" style="left:291px">
    <span class="contact-ico"><svg width="8" height="8" viewBox="0 0 8 8"><path d="M1 0l2 2-1 1.3A5 5 0 0 0 4.7 6L6 5l2 2-1 1C3.5 8 0 4.5 0 1z" fill="var(--orange)"/></svg></span>
    <span>+1 555 014 2288</span>
  </div>
  <div class="abs contact" style="left:377px">
    <span class="contact-ico"><svg width="8" height="6" viewBox="0 0 8 6"><rect width="8" height="6" fill="var(--orange)"/><path d="M0 0l4 3 4-3" fill="none" stroke="#fff" stroke-width=".8"/></svg></span>
    <span>info@kwgrain.example</span>
  </div>
  <div class="abs copy">©Copyright 2015 yoursite. All Rights Reserved.</div>
</footer>

</body>
</html>
```